Classy, Elegant, Simple Business Card Design

Looking to have a classy, simple, and elegant design. Want a top notch designed business card. I really like the look of the new torvane credit card. I also like the design I attached. I am trying to reach 21-29 year old females for booking us for there wedding or event. We offer Disc Jockey Service, Photo Booth Rentals, and Uplighting .

Target Market(s)

21-28 year old females

Contact Information for Business Card

Has to have logo, website, email, and phone number

Font styles to use
Other font styles liked:
• open to font choice, modern, clean
Designer to choose
33a6d7
0791cd
0555a3
ffffff

Requirements
Must have
• Has to have logo, website, email, and phone number
Nice to have
• I really like the design of the new torvane credit card. I also included my logo and some designs I like
Should not have
• clutter or too much info

```html
<!DOCTYPE html>
<html lang="en">
<head>
<meta charset="utf-8">
<title>Brightnote Event Group – Business Card</title>
<link href="https://fonts.googleapis.com/css2?family=Questrial&family=Lato:wght@400&display=swap" rel="stylesheet">
<style>
  :root {
    --backdrop: #2b2b2b;
    --paper: #ffffff;
    --ink: #222222;
    --rule: #555555;
    --muted: #8a8a8a;
    --brand-deep: #0555a3;
    --brand-mid: #0791cd;
    --brand-light: #33a6d7;
    --brand-dark: #0a3f7a;
  }
  * { margin: 0; padding: 0; box-sizing: border-box; }
  html, body {
    width: 1200px; height: 1200px; overflow: hidden;
    background: var(--backdrop);
  }
  .stage { position: relative; width: 1200px; height: 1200px; }
  .card {
    position: absolute; top: 310px; width: 364px; height: 594px;
    box-shadow: 0 3px 8px rgba(0,0,0,.5);
  }
  .card-front { left: 234px; background: var(--paper); }
  .card-back {
    left: 630px; width: 366px;
    background: radial-gradient(ellipse at 45% 50%, var(--brand-mid) 0%, #0a79bd 45%, var(--brand-deep) 100%);
  }
  .wordmark {
    position: absolute; left: 0; right: 0; text-align: center;
    font-family: "Questrial", sans-serif; line-height: 1;
  }
  .card-front .wordmark { top: 230px; }
  .wordmark .name {
    display: block; font-size: 34px; letter-spacing: 0.5px; color: var(--brand-deep);
  }
  .wordmark .tagline {
    display: block; margin-top: 8px; font-size: 13px; letter-spacing: 7px;
    color: var(--muted); padding-left: 7px;
  }
  .card-back .wordmark { top: 478px; }
  .card-back .wordmark .name { color: var(--paper); font-size: 38px; }
  .card-back .wordmark .tagline { color: var(--paper); font-size: 18px; letter-spacing: 8px; margin-top: 10px; }
  .brand-dot {
    position: absolute; left: 50%; top: 148px; width: 56px; height: 56px;
    margin-left: -28px; border-radius: 50%; background: var(--brand-mid);
  }
  .contact-icons {
    position: absolute; left: 87px; top: 370px; width: 190px; height: 24px;
  }
  .contact {
    position: absolute; left: 0; right: 0; top: 405px; text-align: center;
    font-family: "Lato", sans-serif; font-size: 16.5px; line-height: 22px; color: var(--ink);
  }
  .divider {
    position: absolute; left: 85px; width: 195px; top: 488px; height: 1px; background: var(--rule);
  }
  .services {
    position: absolute; left: 0; right: 0; top: 501px; text-align: center;
    font-family: "Lato", sans-serif; font-size: 16.5px; line-height: 22px; color: var(--ink);
  }
</style>
</head>
<body>
<main class="stage">
  <section class="card card-front">
    <span class="brand-dot"></span>
    <div class="wordmark">
      <span class="name">BRIGHTNOTE</span>
      <span class="tagline">EVENT GROUP</span>
    </div>

    <svg class="contact-icons" viewBox="0 0 190 24" aria-hidden="true">
      <line x1="0" y1="12" x2="55" y2="12" stroke="#555" stroke-width="1"/>
      <line x1="135" y1="12" x2="190" y2="12" stroke="#555" stroke-width="1"/>
      <!-- phone -->
      <circle cx="68" cy="12" r="11" fill="#0791cd"/>
      <path d="M62 10 q6 -5 12 0 l-1.5 2 h-2 v-1.5 h-5 v1.5 h-2 z M63.5 13 h9 v4 h-9 z" fill="#fff"/>
      <!-- mail -->
      <circle cx="95" cy="12" r="11" fill="#0791cd"/>
      <rect x="88.5" y="7.5" width="13" height="9" fill="none" stroke="#fff" stroke-width="1.3"/>
      <path d="M88.5 7.5 L95 13 L101.5 7.5" fill="none" stroke="#fff" stroke-width="1.3"/>
      <!-- globe -->
      <circle cx="122" cy="12" r="11" fill="#0791cd"/>
      <circle cx="122" cy="12" r="6" fill="none" stroke="#fff" stroke-width="1.3"/>
      <path d="M116 12 h12 M122 6 q-3.5 6 0 12 M122 6 q3.5 6 0 12" fill="none" stroke="#fff" stroke-width="1"/>
    </svg>

    <p class="contact">
      044-555 010 203<br>
      hello@brightnote.com<br>
      www.brightnote.com
    </p>
    <span class="divider"></span>
    <p class="services">
      Disc Jockey Service | Uplighting<br>
      Photo Booth Rentals
    </p>
  </section>

  <section class="card card-back">
    <div class="wordmark">
      <span class="name">BRIGHTNOTE</span>
      <span class="tagline">EVENT GROUP</span>
    </div>
  </section>
</main>
</body>
</html>
```